Label design for organic saffron, saffron and herbal syrup

We cultivate saffron, Damszen roses, flowers and herbs. We would need a recognizable outfit (label) for our products. Theoretically (and practically) we have "converted" the family coat of arms into a kind of LOGO. I would send this in the attachment. It would be nice if - in one way or another - this LOGO / coat of arms could be used (certainly with other colors). For some time we have played with the idea of changing the second part of the family name "Wallmoser" (in German .... greuth sounds similar to Kraut / herb [English]) .... eg Wallmoser's saffron syrup into the labeling.
Our products are primarily syrups, currently herbal syrup and saffron syrup. Here the first problem arises, the only bottles / caps that are actually approved for syrup filling (hot filling) are appallingly ugly (see attachment), the only possibility of "sprucing up" is to use so-called "shrink sleeves" (here we need a diameter of 31 and a length of about 40), the colors of which are also limited. Besides the syrup, we sell saffron as a spice and various herbal mixtures (see appendix current packaging saffron). Our quantities are small (syrup 200ml-330ml), saffron in the gram range.
We also need quasi the back of the labeling (this should be able to be redefined per charge) .... Batch 1 (with small quantity has eg more of herb xy than the next batch or the saffron syrup with batch xy needs more / less saffron). In addition, we are certified organic (for this reason, the reverse side would also have to contain all the requirements of organic labeling) [see attachment].
We do not really want to address a specific clientele. Maybe just people who want to taste, enjoy, mix drinks, cook .... (and - unfortunately - don't like Corvel syrup :-) and want to pay a bit more, or find our saffron or herbs better than others) .
In summary
- Strong recognition value (possibly inclusion of "coat of arms", color variable ... although I personally don't like yellow that much)
- Saffron syrup (the color of the saffron syrup is yellow / golden-yellow-light orange, in a transparent ugly bottle)
- Herbal syrup (color variable from blue / green / brown / red elements, in transparent ugly bottle)
Saffron and other herbs (very small containers, type of container not yet fixed)
Regarding a potential "style" I can unfortunately give little information. On the one hand, I am in love with minimalism, on the other hand, I find the translucent, cryptic, implied enormously attractive and sometimes even the "overloaded" colorful has its charm. I think that all in all, it just has to be coherent, and then it will be good.
Requirements
Must have
- Integration of Code of Arms, modifiable for different products

```html
<!DOCTYPE html>
<html lang="de">
<head>
<meta charset="utf-8">
<title>Wallmoser Herbal Sirup – Etikett</title>
<link href="https://fonts.googleapis.com/css2?family=Libre+Baskerville:wght@400;700&family=Open+Sans:wght@400;600;700&display=swap" rel="stylesheet">
<style>
  :root {
    --page: #f2f1ec;
    --forest: #1f5a35;
    --forest-deep: #174a2b;
    --gold: #c9a43a;
    --gold-soft: #b8963b;
    --cream: #fcefcb;
    --cream-light: #fdf4da;
    --ink: #3a3326;
    --crest-ink: #3b3a78;
    --badge-green: #8cc63f;
  }
  * { box-sizing: border-box; margin: 0; padding: 0; }
  html, body { width: 849px; height: 1200px; overflow: hidden; background: var(--page); }
  .canvas { position: relative; width: 849px; height: 1200px; }

  .label {
    position: absolute; left: 124px; top: 192px;
    width: 600px; height: 816px;
    background: var(--cream);
    overflow: hidden;
    box-shadow: 0 0 0 1px rgba(0,0,0,.08);
  }

  .label__crown { position: absolute; left: 0; top: 0; width: 600px; height: 295px; }
  .label__gold-rule { position: absolute; left: 0; top: 295px; width: 600px; height: 7px; background: var(--gold); }

  .brand {
    position: absolute; left: 150px; top: 90px; width: 300px;
    text-align: center;
  }
  .brand__mark {
    width: 70px; height: 70px; border-radius: 50%;
    margin: 0 auto 18px; background: var(--crest-ink); opacity: .85;
  }
  .brand__name {
    font-family: "Libre Baskerville", serif; font-size: 34px;
    color: var(--crest-ink); letter-spacing: .5px;
  }

  .product-panel { position: absolute; left: 172px; top: 302px; width: 258px; height: 310px; }
  .product-name {
    position: absolute; left: 172px; top: 382px; width: 258px;
    text-align: center;
    font-family: "Libre Baskerville", serif; font-size: 48px; line-height: 54px;
    color: var(--cream-light);
  }

  .side-text { position: absolute; }
  .side-text__inner {
    position: absolute; left: 0;
    transform-origin: top left; transform: rotate(-90deg);
    font-family: "Open Sans", sans-serif; color: var(--ink);
  }
  .ingredients { left: 16px; top: 345px; width: 100px; height: 463px; }
  .ingredients .side-text__inner { top: 463px; width: 463px; height: 100px; font-size: 12.5px; line-height: 16.5px; font-weight: 600; }
  .producer { left: 500px; top: 345px; width: 56px; height: 290px; }
  .producer .side-text__inner { top: 290px; width: 290px; height: 56px; font-size: 10px; line-height: 13.5px; font-weight: 600; }

  .best-before {
    position: absolute; left: 504px; top: 653px; width: 68px; height: 154px;
    background: #fff; border: 1.5px solid var(--ink);
  }
  .best-before .side-text__inner { top: 150px; width: 150px; height: 64px; padding: 6px 10px; font-size: 12px; font-weight: 700; }

  .organic-badge {
    position: absolute; left: 262px; top: 676px; width: 74px; height: 118px;
    background: var(--badge-green); border-radius: 4px;
  }
  .organic-badge::after {
    content: ""; position: absolute; left: 12px; top: 14px; width: 50px; height: 50px;
    border-radius: 50%; background: #fff; opacity: .85;
  }
  .spec {
    position: absolute; top: 782px;
    font-family: "Open Sans", sans-serif; font-size: 16px; color: var(--ink);
  }
  .spec--volume { left: 188px; }
  .spec--ratio { left: 362px; }
</style>
</head>
<body>
<main class="canvas">
  <section class="label" aria-label="Etikett Herbal Sirup">
    <svg class="label__crown" viewBox="0 0 600 295" role="img" aria-label="Dunkelgrünes Band mit goldenem Blumenornament, mittig ausgespart für das Wappen">
      <defs>
        <radialGradient id="crownTone" cx="50%" cy="50%" r="70%">
          <stop offset="0" stop-color="#2b6a40"/>
          <stop offset="1" stop-color="#174a2b"/>
        </radialGradient>
      </defs>
      <rect width="600" height="295" fill="url(#crownTone)"/>
      <path d="M236 0 H365 Q352 20 360 40 A160 160 0 0 1 455 185 A154 154 0 0 1 440 295 H160 A154 154 0 0 1 146 185 A160 160 0 0 1 242 40 Q250 20 236 0 Z" fill="#ffffff"/>
      <path d="M160 295 A154 154 0 0 1 146 185 A160 160 0 0 1 242 40" fill="none" stroke="#c9a43a" stroke-width="3"/>
      <path d="M440 295 A154 154 0 0 0 455 185 A160 160 0 0 0 360 40" fill="none" stroke="#c9a43a" stroke-width="3"/>
    </svg>
    <div class="brand">
      <div class="brand__mark"></div>
      <div class="brand__name">Wallmoser</div>
    </div>
    <div class="label__gold-rule"></div>

    <svg class="product-panel" viewBox="0 0 258 310" role="img" aria-label="Grünes Feld mit zarter Kräuterzeichnung">
      <path d="M0 0 H258 V181 A129 129 0 0 1 0 181 Z" fill="#1f5a35"/>
      <path d="M8 0 V181 A121 121 0 0 0 250 181 V0" fill="none" stroke="#c9a43a" stroke-width="2.5"/>
    </svg>
    <h1 class="product-name">Herbal<br>Sirup</h1>

    <div class="side-text ingredients">
      <p class="side-text__inner"><strong>ZUTATEN:</strong> Lorem ipsum dolor sit amet, consectetur adipiscing elit. Morbi ultricies, nunc vel euismod mattis, metus sem tincidunt nisl, vitae mollis diam mi eget ante. Aliquam id sollicitudin turpis, vivamus aliquet elit sem, et ornare ex aliquam in.</p>
    </div>
    <div class="side-text producer">
      <p class="side-text__inner">*aus kontrolliert biologischer Landwirtschaft<br>Carefully made by Wallmoser Farm<br>1234 Street Name, Any City, District, Country</p>
    </div>
    <div class="side-text best-before">
      <p class="side-text__inner">Best Before:</p>
    </div>

    <div class="organic-badge" aria-hidden="true"></div>
    <span class="spec spec--volume">200mL</span>
    <span class="spec spec--ratio">1:7</span>
  </section>
</main>
</body>
</html>
```